Classy, Elegant, Simple Business Card Design

Looking to have a classy, simple, and elegant design. Want a top notch designed business card. I really like the look of the new torvane credit card. I also like the design I attached. I am trying to reach 21-29 year old females for booking us for there wedding or event. We offer Disc Jockey Service, Photo Booth Rentals, and Uplighting .

Target Market(s)

21-28 year old females

Contact Information for Business Card

Has to have logo, website, email, and phone number

Font styles to use
Other font styles liked:
• open to font choice, modern, clean
Designer to choose
33a6d7
0791cd
0555a3
ffffff

Requirements
Must have
• Has to have logo, website, email, and phone number
Nice to have
• I really like the design of the new torvane credit card. I also included my logo and some designs I like
Should not have
• clutter or too much info

```html
<!DOCTYPE html>
<html lang="en">
<head>
<meta charset="UTF-8">
<title>Tidewell Event Group – Business Card</title>
<link rel="stylesheet" href="https://fonts.googleapis.com/css2?family=Oswald:wght@500&family=Work+Sans:wght@400;500&display=swap">
<style>
  :root {
    --backdrop: #141414;
    --card: #1f1f1f;
    --card-light: #2a2a2a;
    --blue: #0791cd;
    --blue-deep: #0555a3;
    --blue-bright: #33a6d7;
    --white: #ffffff;
    --grey: #bdbdbd;
  }
  * { margin: 0; padding: 0; box-sizing: border-box; }
  html, body {
    width: 1200px; height: 900px; overflow: hidden;
    background: var(--backdrop);
    font-family: "Work Sans", Arial, sans-serif;
    color: var(--white);
  }
  .canvas {
    width: 1200px; height: 900px;
    display: flex; flex-direction: column; align-items: center; justify-content: center;
    gap: 30px;
  }
  .card {
    position: relative;
    width: 700px; height: 400px;
    background: linear-gradient(135deg, var(--card) 0%, var(--card) 55%, var(--card-light) 100%);
    border-bottom: 4px solid var(--blue);
    overflow: hidden;
  }
  /* Front */
  .card-front .brand {
    position: absolute; top: 130px; left: 0; right: 0;
    display: flex; align-items: center; justify-content: center; gap: 14px;
  }
  .brand-dot {
    width: 18px; height: 18px; border-radius: 50%;
    background: var(--blue);
  }
  .brand-name {
    font-family: "Work Sans", Arial, sans-serif;
    font-weight: 500; font-size: 40px; letter-spacing: 2px;
    color: var(--blue-bright);
  }
  .services {
    position: absolute; bottom: 38px; left: 0; right: 0;
    text-align: center; font-size: 18px; letter-spacing: 1px;
    word-spacing: 4px;
  }
  .services span + span { margin-left: 14px; }
  /* Back */
  .identity {
    position: absolute; top: 150px; left: 70px; width: 250px;
    text-align: right;
  }
  .person-name {
    font-family: "Oswald", "Arial Narrow", sans-serif;
    font-weight: 500; font-size: 44px; line-height: 1;
    color: var(--blue); letter-spacing: 1px;
  }
  .person-role { font-size: 19px; margin-top: 6px; letter-spacing: 1px; }
  .divider {
    position: absolute; top: 150px; left: 345px;
    width: 2px; height: 74px; background: var(--blue);
  }
  .contact-list {
    position: absolute; top: 148px; left: 375px;
    list-style: none; font-size: 19px; letter-spacing: 0.5px; line-height: 27px;
  }
  .contact-list li { display: flex; align-items: center; gap: 12px; }
  .contact-list svg { width: 14px; height: 14px; flex: none; }
  .highlight { color: var(--blue); }
  .address {
    position: absolute; bottom: 34px; left: 70px;
    font-size: 20px; letter-spacing: 1px;
  }
</style>
</head>
<body>
<main class="canvas">
  <section class="card card-front">
    <div class="brand">
      <span class="brand-dot"></span>
      <span class="brand-name">Tidewell Event Group</span>
    </div>
    <p class="services"><span>Disc Jockeys</span><span>Photo Booths</span><span>And More</span></p>
  </section>

  <section class="card card-back">
    <div class="identity">
      <h1 class="person-name">DANIEL HARROW</h1>
      <p class="person-role">Managing Partner</p>
    </div>
    <div class="divider"></div>
    <ul class="contact-list">
      <li>
        <svg viewBox="0 0 16 16" aria-hidden="true"><path d="M4 1.5l2 3-1.3 1.3a8 8 0 0 0 5.5 5.5L11.5 10l3 2-1 2.5C7 14.5 1.5 9 1.5 2.5z" fill="none" stroke="var(--blue)" stroke-width="1.4"/></svg>
        555-014-2290
      </li>
      <li>
        <svg viewBox="0 0 16 16" aria-hidden="true"><rect x="1.5" y="3.5" width="13" height="9" fill="none" stroke="var(--blue)" stroke-width="1.4"/><path d="M1.5 3.5L8 9l6.5-5.5" fill="none" stroke="var(--blue)" stroke-width="1.4"/></svg>
        info@tidewell.com
      </li>
      <li>
        <svg viewBox="0 0 16 16" aria-hidden="true"><circle cx="8" cy="8" r="6.5" fill="none" stroke="var(--blue)" stroke-width="1.3"/><ellipse cx="8" cy="8" rx="3" ry="6.5" fill="none" stroke="var(--blue)" stroke-width="1.1"/><path d="M1.5 8h13" stroke="var(--blue)" stroke-width="1.1"/></svg>
        <span>www.<span class="highlight">tidewell</span>.com</span>
      </li>
    </ul>
    <p class="address">118 W Linden Ave., Marlow Park, CA 90000</p>
  </section>
</main>
</body>
</html>
```